Pediatric Therapy Clinic Brochure

We need a Brochure for a new pediatric therapy clinic. The clinic offers occupational therapy, physical therapy, speech therapy and feeding therapy. We want a brochure for parents, doctors and medical professional. It should have a fun and inviting, but still professional feel. Should be kid focused, bright and colorful. All the text / wording is there and a rough layout. Now I need someone to tidy and jazz it up and make it look professional.

Target Market(s)

Parents, doctors, medical professional

Industry/Entity Type

Medical

Font styles to use
Serif
Sans Serif

Requirements
Must have
• Keep All the text with information about services the same. Logo on front. Pictures throughout (use any of the pictures provided) (try and match up with corresponding service) (pictures are labeled). Need to have Map and contact info
• Keep colors consistent with our logo
Nice to have
• Background, special effects. Make it look fancy and professional
Should not have
• Not so busy that is takes away from the text

```html
<!DOCTYPE html>
<html lang="en">
<head>
<meta charset="utf-8">
<title>Children's Therapy Brochure – Inside Spread</title>
<link rel="stylesheet" href="https://fonts.googleapis.com/css2?family=Oswald:wght@600;700&family=Arimo:wght@400;700&display=swap">
<style>
  :root {
    --stage: #9d9d9f;
    --paper: #f7f7f8;
    --paper-shade: #ececee;
    --yellow: #f2c417;
    --yellow-deep: #e0ad0d;
    --orange: #e3691c;
    --blue: #1a4f9c;
    --rule: #1a4f9c;
  }
  * { box-sizing: border-box; margin: 0; padding: 0; }
  html, body { width: 1200px; height: 1200px; overflow: hidden; }
  body {
    background: linear-gradient(180deg, #8c8c8e 0%, var(--stage) 55%, #b4b4b5 100%);
    font-family: "Arimo", Arial, sans-serif;
    position: relative;
  }
  .brochure {
    position: absolute; left: 30px; top: 160px;
    width: 1140px; height: 880px;
    background: var(--paper);
    display: grid; grid-template-columns: repeat(3, 1fr);
    box-shadow: 0 18px 40px rgba(0,0,0,.25);
    overflow: hidden;
  }
  .trim { position: absolute; inset: 0; width: 100%; height: 100%; pointer-events: none; }
  .panel {
    position: relative; z-index: 1;
    padding: 46px 34px 40px;
    display: flex; flex-direction: column;
  }
  .panel + .panel { border-left: 1px solid var(--paper-shade); }
  .photo {
    border: 9px solid var(--orange); border-radius: 22px;
    box-shadow: 0 4px 10px rgba(0,0,0,.25);
  }
  .photo--top { height: 190px; margin: 8px 4px 22px;
    background: linear-gradient(135deg, #f1e9e3 0%, #e8b9a0 45%, #c94a3a 70%, #f0ece8 100%); }
  .photo--bottom { height: 180px; margin-top: auto;
    background: linear-gradient(120deg, #d9c3a6 0%, #caa07e 40%, #7f8fb0 75%, #e4dfe5 100%); }
  .service { margin-bottom: 18px; }
  .service__title {
    font-family: "Oswald", Impact, sans-serif; font-weight: 700;
    color: var(--blue); font-size: 31px; line-height: 1.05;
    text-align: center; letter-spacing: .3px;
  }
  .service__intro {
    color: var(--blue); font-size: 13.5px; line-height: 1.3;
    text-align: center; margin: 4px 6px 0;
  }
  .service__rule { border: 0; border-top: 3px solid var(--rule); margin: 10px 0 12px; }
  .service__list { list-style: none; }
  .service__list li {
    color: var(--orange); font-weight: 700; font-size: 14.5px;
    line-height: 1.3; padding-left: 14px; position: relative;
  }
  .service__list li::before { content: "•"; position: absolute; left: 0; }
  .brand {
    margin-top: auto; display: flex; align-items: center; justify-content: center; gap: 10px;
    color: var(--blue); font-family: "Arimo", Arial, sans-serif; font-weight: 700;
    font-size: 24px; line-height: 1.1; text-align: center;
  }
  .brand__dot { width: 18px; height: 18px; border-radius: 50%; background: var(--orange); flex: none; }
  .corner-note {
    position: absolute; right: 16px; bottom: 30px; z-index: 2;
    width: 130px; text-align: center;
    font-size: 13px; font-weight: 700; color: #2a2a2a; line-height: 1.25;
  }
</style>
</head>
<body>
  <main class="brochure">
    <svg class="trim" viewBox="0 0 1140 880" preserveAspectRatio="none" aria-hidden="true">
      <polygon points="0,0 240,0 0,110" fill="var(--yellow)"/>
      <polygon points="380,0 1140,0 1140,22 760,34 380,22" fill="var(--yellow)"/>
      <polygon points="0,862 1140,836 1140,880 0,880" fill="var(--yellow)"/>
      <polygon points="1140,560 1140,880 900,880" fill="var(--yellow)"/>
      <polygon points="1140,600 1140,880 960,880" fill="var(--yellow-deep)" opacity=".35"/>
    </svg>

    <section class="panel panel--left">
      <div class="photo photo--top" role="img" aria-label="Photo of a smiling boy showing paint-covered hands"></div>
      <article class="service">
        <h2 class="service__title">OCCUPATIONAL THERAPY</h2>
        <p class="service__intro">Helping children build better self-esteem, confidence and independence in all the things they do.</p>
        <hr class="service__rule">
        <ul class="service__list">
          <li>Sensory Processing Disorder</li>
          <li>Balance, Coordination, Strength, and Endurance</li>
          <li>Fine Motor and Handwriting</li>
          <li>Visual- Motor Integration</li>
          <li>Play and Social Skills</li>
          <li>Feeding and Oral Motor Skills</li>
          <li>Self-Care</li>
          <li>Academic and Cognitive Skills</li>
          <li>Behavioral Difficulties</li>
          <li>Developmental Delays</li>
        </ul>
      </article>
      <div class="photo photo--bottom" role="img" aria-label="Photo of three children whispering and smiling"></div>
    </section>

    <section class="panel panel--middle">
      <article class="service">
        <h2 class="service__title">SPEECH THERAPY</h2>
        <p class="service__intro">Helping children speak, communicate and understand language.</p>
        <hr class="service__rule">
        <ul class="service__list">
          <li>Expressive and Receptive Language</li>
          <li>Speech and Language Developmental Milestones</li>
          <li>Articulation / Intelligibility</li>
          <li>Speech Fluency</li>
          <li>Pragmatics and Social Skills</li>
          <li>Literacy and Vocabulary</li>
          <li>Apraxia of Speech</li>
          <li>Augmentative and Alternative Communication</li>
          <li>Feeding and Oral Motor</li>
        </ul>
      </article>
      <article class="service">
        <h2 class="service__title">SENSORY INTEGRATION</h2>
        <p class="service__intro">Gradually increasing play based activities to improve a child's nervous system. Helping children learn to self-regulate their emotions, behaviors and arousal levels.</p>
        <hr class="service__rule">
        <ul class="service__list">
          <li>Autism and ADHD</li>
          <li>Sensory Processing Disorder</li>
          <li>Poor Tolerance of Sensory Stimuli from the Environment</li>
          <li>Meltdowns and Tantrums</li>
          <li>Poor Balance/Body Awareness</li>
          <li>Poor Attention and Concentration</li>
          <li>Poor Self-Regulation</li>
          <li>Behavior and Social Difficulties</li>
          <li>Poor Motor Coordination and Motor Planning</li>
          <li>Aggression, Frustration or Avoidance Behaviors</li>
        </ul>
      </article>
      <div class="brand"><span class="brand__dot"></span><span>Brightpath Children's Therapy</span></div>
    </section>

    <section class="panel panel--right">
      <article class="service">
        <h2 class="service__title">FEEDING THERAPY</h2>
        <p class="service__intro">Providing skilled assessment and intervention to children with feeding difficulties.</p>
        <hr class="service__rule">
        <ul class="service__list">
          <li>Food Aversions</li>
          <li>Food Refusal</li>
          <li>Very Picky Eating</li>
          <li>Avoidance of Certain Textures</li>
          <li>Gagging and Vomiting</li>
          <li>Oral Motor/ Chewing Difficulties</li>
          <li>Limited Diet/Food Repertoire</li>
        </ul>
      </article>
      <article class="service">
        <h2 class="service__title">PHYSICAL THERAPY</h2>
        <p class="service__intro">Helping children move and interact within their environment smoothly and confidently.</p>
        <hr class="service__rule">
        <ul class="service__list">
          <li>Torticollis</li>
          <li>Walking and Mobility</li>
          <li>Developmental Motor Milestones</li>
          <li>Balance, Coordination, Motor Planning</li>
          <li>Strength, Muscle Tone and Range of Motion</li>
          <li>Sports Injuries</li>
          <li>Toe Walking</li>
          <li>Myofascial Release</li>
          <li>Postural Control and Positioning</li>
        </ul>
      </article>
      <article class="service">
        <h2 class="service__title">GROUP THERAPY</h2>
        <p class="service__intro">Using peer role models to learn new and challenging skills.</p>
        <hr class="service__rule">
        <ul class="service__list">
          <li>Social Groups</li>
          <li>Feeding Groups</li>
        </ul>
      </article>
    </section>

    <p class="corner-note">**More Group Classes Coming Soon</p>
  </main>
</body>
</html>
```